Dynamic Business Card for Sports Supplements Company

Hi! I'm looking for an awesome business card to match my existing sports supplement company. I have uploaded my current company logo and screenshot of the front page of my website.

I would like to have something dynamic and interesting and utilize the colors in the website - the reds and purples

The business card should be double sided and focus on a unique eye-catching design on the back and include all the relevant company info.

Most importantly, it should say somewhere: "Sign up on our website for a coupon code."

Target Market(s)

Mostly for women gym goers but it shouldn't be too feminine. It should be in keeping with the website design. It should flow and clearly be connected to it

Industry/Entity Type

Business

Contact Information for Business Card

Lorraine K. Vestal
CEO
LVestal@Quorvanexco.com
www.quorvanexco.com
555.417.3820
P.O. Box 47315
Fenwick, Ohio 00000

Sign up on our website for a coupon code

Font styles to use
Serif
Sans Serif
Other font styles liked:
• Novecento font family and "Quorvanex" is in AR Destine font

Requirements
Must have
• One side should be a bold Quorvanex logo design. Even just the symbol itself may be o.k. (see attached file)

```html
<!DOCTYPE html>
<html lang="en">
<head>
<meta charset="utf-8">
<title>Quorvanex Business Card</title>
<link rel="stylesheet" href="https://fonts.googleapis.com/css2?family=Open+Sans:ital,wght@0,400;0,600;0,800;1,400&display=swap">
<style>
  :root {
    --purple: #5e4680;
    --purple-deep: #4a3568;
    --red: #e41f26;
    --white: #ffffff;
    --backdrop-1: #8a9296;
    --backdrop-2: #4f575c;
  }
  * { margin: 0; padding: 0; box-sizing: border-box; }
  html, body { width: 1200px; height: 900px; overflow: hidden; }
  body {
    background: radial-gradient(circle at 50% 45%, var(--backdrop-1), var(--backdrop-2));
    font-family: "Open Sans", Arial, sans-serif;
    position: relative;
  }
  .card {
    position: absolute;
    left: 250px;
    width: 700px;
    height: 400px;
    overflow: hidden;
    box-shadow: 0 10px 30px rgba(0,0,0,0.35);
  }
  .card-front { top: 35px; background: var(--white); }
  .card-back { top: 465px; background: var(--purple); }

  .front-shape { position: absolute; inset: 0; width: 100%; height: 100%; }

  .brand {
    position: absolute;
    left: 70px;
    top: 40px;
    display: flex;
    align-items: center;
    gap: 12px;
  }
  .brand-mark { width: 22px; height: 22px; background: var(--purple); }
  .brand-name {
    font-weight: 800;
    font-size: 34px;
    color: var(--purple);
    letter-spacing: 1px;
    text-transform: uppercase;
    line-height: 1;
  }
  .brand-tagline {
    position: absolute;
    left: 104px;
    top: 80px;
    font-size: 12px;
    color: var(--purple);
    letter-spacing: 1px;
  }

  .contact {
    position: absolute;
    left: 34px;
    top: 175px;
    color: var(--white);
    font-size: 15px;
    list-style: none;
  }
  .contact li { display: flex; align-items: center; gap: 10px; margin-bottom: 6px; }
  .contact-icon {
    width: 18px; height: 18px;
    background: var(--white);
    border-radius: 3px;
    display: flex; align-items: center; justify-content: center;
  }
  .contact-note {
    position: absolute;
    left: 34px;
    top: 282px;
    color: var(--white);
    font-size: 12.5px;
    font-style: italic;
  }

  .person {
    position: absolute;
    right: 58px;
    top: 178px;
    text-align: right;
  }
  .person-name { color: var(--red); font-size: 22px; }
  .person-role { color: var(--purple); font-size: 14px; font-weight: 600; }

  .address {
    position: absolute;
    right: 120px;
    bottom: 26px;
    color: var(--white);
    font-size: 16px;
    font-style: normal;
    text-align: right;
    line-height: 1.35;
  }

  .back-brand {
    position: absolute;
    left: 0; right: 0;
    top: 130px;
    text-align: center;
    color: var(--white);
  }
  .back-name {
    font-weight: 800;
    font-size: 78px;
    letter-spacing: 2px;
    text-transform: uppercase;
    line-height: 1;
  }
  .back-tagline {
    margin-top: 14px;
    font-size: 26px;
    letter-spacing: 6px;
  }
</style>
</head>
<body>

<section class="card card-front" aria-label="Business card front">
  <svg class="front-shape" viewBox="0 0 700 400" preserveAspectRatio="none" aria-hidden="true">
    <path d="M0,140 C190,110 300,170 360,250 C420,330 520,345 700,300 L700,400 L0,400 Z" fill="var(--purple)"/>
    <path d="M0,122 C190,92 310,150 372,236 C430,318 520,330 700,282" fill="none" stroke="var(--red)" stroke-width="9"/>
    <path d="M0,133 C190,103 304,160 365,244 C424,325 520,338 700,292" fill="none" stroke="var(--white)" stroke-width="5"/>
  </svg>

  <div class="brand">
    <span class="brand-mark"></span>
    <span class="brand-name">Quorvanex</span>
  </div>
  <p class="brand-tagline">your daily training ally</p>

  <ul class="contact">
    <li>
      <span class="contact-icon">
        <svg width="12" height="12" viewBox="0 0 24 24"><path d="M6 2h4l2 5-3 2a12 12 0 0 0 6 6l2-3 5 2v4a2 2 0 0 1-2 2A18 18 0 0 1 4 4a2 2 0 0 1 2-2z" fill="var(--red)"/></svg>
      </span>555.417.3820
    </li>
    <li>
      <span class="contact-icon">
        <svg width="12" height="12" viewBox="0 0 24 24"><rect x="2" y="5" width="20" height="14" fill="var(--red)"/><path d="M2 5l10 8 10-8" fill="none" stroke="var(--white)" stroke-width="2"/></svg>
      </span>LVestal@Quorvanexco.com
    </li>
    <li>
      <span class="contact-icon">
        <svg width="12" height="12" viewBox="0 0 24 24"><circle cx="12" cy="12" r="10" fill="none" stroke="var(--red)" stroke-width="2.5"/><path d="M2 12h20M12 2c4 4 4 16 0 20M12 2c-4 4-4 16 0 20" fill="none" stroke="var(--red)" stroke-width="2"/></svg>
      </span>www.quorvanexco.com
    </li>
  </ul>
  <p class="contact-note">Sign up on our website for a coupon code</p>

  <div class="person">
    <p class="person-name">Lorraine K. Vestal</p>
    <p class="person-role">CEO</p>
  </div>

  <address class="address">
    P.O. Box 47315<br>Fenwick, Ohio 00000
  </address>
</section>

<section class="card card-back" aria-label="Business card back">
  <div class="back-brand">
    <p class="back-name">Quorvanex</p>
    <p class="back-tagline">your daily training ally</p>
  </div>
</section>

</body>
</html>
```